Redesign of an existing homepage

This site needs a redesign
https://www.wanderhof-kelbach.de
This page with the accommodation options is important for the customer
https://www.wanderhof-kelbach.de/gastgeber/
Till now there is a new logo. See attachment. That's all I have.
It would make sense to use the colors of the logo in the redesign.
footer.jpg.
I would put this info into the footer. The graphic (Infomaterial) is not needed.
a new menu - links.jpg
This info can be put in a new menu. Therefore the right column is gone and there is more space for the design.
NEW:
Please keep in mind that the Icons are important and shall be displayed under every accommodation

```html
<!DOCTYPE html>
<html lang="de">
<head>
<meta charset="utf-8">
<title>Tourismusverband Kelbach</title>
<link href="https://fonts.googleapis.com/css2?family=Poppins:wght@400;500;600;700;800&display=swap" rel="stylesheet">
<style>
:root{
  --blue:#0b72b9;
  --blue-light:#3aa7dd;
  --green:#7bb62a;
  --star:#f7a21b;
  --ink:#111;
  --text:#333;
  --band:#eef7fd;
  --quote:#e1e7f0;
}
*{box-sizing:border-box;margin:0;padding:0}
html,body{width:1200px;height:3089px;overflow:hidden}
body{position:relative;font-family:'Poppins',sans-serif;color:var(--text);background:#fff}
.abs{position:absolute}
.btn{position:absolute;display:flex;align-items:center;justify-content:center;background:var(--blue);color:#fff;border-radius:22px;font-size:14px;font-weight:600;height:42px}
.btn-inline{display:inline-flex;align-items:center;justify-content:center;background:var(--blue);color:#fff;border-radius:22px;font-size:14px;font-weight:600;height:42px;width:129px;margin-top:14px}
.accent{color:var(--blue)}

/* hero */
.hero-glow{left:0;top:0;width:1200px;height:620px;background:radial-gradient(ellipse at 10% 40%,#e8f1fa 0%,#fff 55%)}
.hero-art{left:0;top:0}
.nav{left:124px;top:22px;width:952px;height:76px;background:#fff;border-radius:38px;box-shadow:0 6px 24px rgba(0,0,0,.08)}
.brand{position:absolute;left:32px;top:16px;display:flex;align-items:center;gap:8px}
.brand-dot{width:36px;height:36px;border-radius:50%;background:var(--green)}
.brand-name{font-size:11px;font-weight:700;color:var(--blue);line-height:13px;text-transform:uppercase}
.menu{position:absolute;right:137px;top:0;height:76px;display:flex;align-items:center;gap:24px;font-size:13.5px;font-weight:500;color:var(--ink);white-space:nowrap}
.nav .btn{left:839px;top:17px;width:93px;font-size:14px}
.hero-title{left:142px;top:230px;font-size:37px;font-weight:800;line-height:46px;color:var(--ink);text-transform:uppercase}

/* intro */
.intro-back{left:142px;top:706px;width:307px;height:422px;border-radius:14px;background:linear-gradient(180deg,#e6f1fb,#eaf6ee)}
.intro-photo{left:162px;top:656px;width:301px;height:454px;border-radius:10px;background:linear-gradient(170deg,#f4efe3 0%,#b8b79a 40%,#7e8a4e 75%,#a48a5e 100%)}
.intro-title{left:542px;top:662px;width:520px;font-size:31px;font-weight:600;line-height:40px;color:var(--ink)}
.intro-body{left:542px;top:758px;width:512px;font-size:13px;line-height:22px}
.intro-body p{margin-bottom:6px}

/* hosts */
.hosts{left:0;top:1214px;width:1200px;height:490px;background:var(--band)}
.sec-title{position:absolute;left:0;width:1200px;text-align:center;font-size:29px;font-weight:600;color:var(--ink)}
.host{position:absolute;top:1360px;width:292px;height:172px;border-radius:10px}
.host-info{position:absolute;left:21px;top:130px;width:249px;height:75px;background:var(--blue-light);border-radius:8px;color:#fff;padding:11px 14px 0 15px}
.host-info h3{font-size:13px;font-weight:700;margin-bottom:5px}
.host-info p{font-size:9.5px;line-height:14px}
.host-go{position:absolute;right:10px;top:22px;width:31px;height:31px;border-radius:50%;background:#fff;display:flex;align-items:center;justify-content:center}

/* testimonials */
.review{position:absolute;top:1878px;width:517px;height:294px;text-align:center}
.review.main{background:#fff;border-radius:16px;box-shadow:0 8px 40px rgba(11,114,185,.08)}
.avatar{position:absolute;left:50%;top:34px;width:66px;height:66px;margin-left:-33px;border-radius:50%;border:3px solid #fff;box-shadow:0 3px 10px rgba(0,0,0,.15);background:linear-gradient(160deg,#c9a07f,#6b4a35)}
.quote{position:absolute;left:42px;top:80px}
.stars{position:absolute;left:0;width:100%;top:116px;color:var(--star);font-size:17px;letter-spacing:3px}
.review h4{position:absolute;left:0;width:100%;top:143px;font-size:16px;font-weight:600;color:var(--ink)}
.review p{position:absolute;left:18px;right:18px;top:204px;font-size:12.5px;line-height:22.5px}

/* map */
.map{left:142px;top:2339px;width:918px;height:246px;border-radius:14px;background:linear-gradient(180deg,#e6f1fb,#ebf6ee)}
.map a{position:absolute;left:0;width:918px;top:144px;text-align:center;font-size:13px;font-weight:600;color:var(--ink)}

/* footer */
.footer{left:0;top:2671px;width:1200px;height:418px;background:var(--blue);color:#fff}
.f-brand{position:absolute;left:142px;top:68px;text-align:center;width:195px}
.f-brand .brand-dot{width:76px;height:76px;margin:0 auto 12px;background:var(--green)}
.f-brand span{display:block;font-size:19px;font-weight:700;line-height:22px;text-transform:uppercase}
.f-addr{position:absolute;left:142px;top:226px;font-size:13px;line-height:21px}
.f-col{position:absolute;top:76px;font-size:13px}
.f-col h5{font-size:17px;font-weight:600;margin-bottom:20px}
.f-col li{list-style:none;line-height:30px}
.f-col .lines{line-height:22px}
.f-rule{position:absolute;left:142px;top:359px;width:918px;height:1px;background:rgba(255,255,255,.35)}
.f-copy{position:absolute;left:142px;top:377px;font-size:13px}
.socials{position:absolute;left:927px;top:374px;display:flex;gap:9px}
.socials span{width:27px;height:27px;border-radius:50%;background:#fff}
</style>
</head>
<body>

<div class="abs hero-glow"></div>
<svg class="abs hero-art" width="1200" height="560" viewBox="0 0 1200 560">
  <defs>
    <linearGradient id="photoTone" x1="0" y1="0" x2="1" y2="1">
      <stop offset="0" stop-color="#d6a25a"/>
      <stop offset=".45" stop-color="#8d7a55"/>
      <stop offset="1" stop-color="#b9ad93"/>
    </linearGradient>
  </defs>
  <path d="M560,95 C552,130 552,165 560,200 L575,200 C566,160 566,120 575,95 Z" fill="#d8ecf8"/>
  <path d="M1100,430 C1150,400 1180,380 1200,360 L1200,400 C1160,430 1120,445 1080,450 Z" fill="#e4f1d4"/>
  <path d="M1080,425 C1130,380 1170,330 1200,305 L1200,330 C1170,360 1130,400 1090,430 Z" fill="var(--blue)"/>
  <path role="img" aria-label="Foto: junge Familie beim Spaziergang auf einem herbstlichen Feldweg" d="M600,0 L1200,0 L1200,312 C1120,380 1070,470 970,496 C860,520 760,470 690,382 C620,292 562,205 568,105 C572,55 588,22 600,0 Z" fill="url(#photoTone)"/>
</svg>

<nav class="abs nav">
  <div class="brand"><span class="brand-dot"></span><span class="brand-name">Tourismusverband<br>Kelbach</span></div>
  <div class="menu"><span>Kelbach</span><span>Kelbachtal-Land</span><span>Quellenland</span><span>Tourismusverband</span><span>Hügelland</span></div>
  <span class="btn">Kontakt</span>
</nav>

<h1 class="abs hero-title">Fremdenverkehrsver<br>ein Kelbach und<br>Umgebung</h1>
<span class="btn" style="left:142px;top:403px;width:129px">Mehr Erfahren</span>

<div class="abs intro-back"></div>
<div class="abs intro-photo" role="img" aria-label="Foto: Familie geht Hand in Hand über einen Wiesenweg zwischen Kiefern"></div>
<h2 class="abs intro-title"><span class="accent">Urlaub Im Kelbachtal</span> - Dem Schönsten Fleck Des Hügellands</h2>
<div class="abs intro-body">
  <p>Lieber Besucherinnen und Besucher,</p>
  <p>Kelbach und Umgebung haben all das, was das Leben lebenswert macht: Kultur und Natur, Lebensfreude und Genuss, freundliche und aufgeschlossene Menschen...</p>
  <p>Ob Kirchen, Brunnen oder andere Baudenkmäler – bei einem Rundgang durch die Kelbacher Wanderstadt kann man viele liebevolle Details entdecken.</p>
  <p>Für Bewegungsfreudige und Erholungssuchende gibt es “Natur pur” in und um Kelbach! Hier kann man sportlich unterwegs sein beim Radeln, Walken, Wandern, Golfen, Reiten und Baden oder einfach nur die Ruhe genießen.</p>
  <p>Freizeit und Erholung für die ganze Familie – planen Sie einen Urlaub auf dem Bauernhof, in einer Ferienwohnung oder im Hotel. Ihr Urlaub im Kelbachtal wird ein einmaliges Erlebnis!</p>
  <span class="btn-inline">Mehr Erfahren</span>
</div>

<section class="abs hosts"></section>
<h2 class="sec-title" style="top:1283px">Gastgeber Im <span class="accent">Kelbachtal</span></h2>

<div class="host" style="left:142px;background:linear-gradient(180deg,#dfeaf2,#8a9a7a 60%,#6d7f5a)" role="img" aria-label="Luftbild eines Campingplatzes zwischen Feldern">
  <div class="host-info"><h3>Wiesencamp Lindau C</h3><p>Lindenweg 4, 94199 Lindau<br>Wohneinheiten</p>
  <span class="host-go"><svg width="13" height="13" viewBox="0 0 13 13"><path d="M3 10 L10 3 M4.5 3 H10 V8.5" stroke="#0b72b9" stroke-width="1.6" fill="none"/></svg></span></div>
</div>
<div class="host" style="left:455px;background:linear-gradient(180deg,#8fb0c8,#4a3b2c 50%,#5f7a45)" role="img" aria-label="Holzhaus mit Balkon im Grünen">
  <div class="host-info"><h3>Mühlenhäusl</h3><p>Auweg 7, 84399 Tannried<br>1 Wohneinheit</p>
  <span class="host-go"><svg width="13" height="13" viewBox="0 0 13 13"><path d="M3 10 L10 3 M4.5 3 H10 V8.5" stroke="#0b72b9" stroke-width="1.6" fill="none"/></svg></span></div>
</div>
<div class="host" style="left:768px;background:linear-gradient(180deg,#c9d6dc,#5a4a3a 45%,#cfc9bd 75%,#6b7d55)" role="img" aria-label="Landhaus mit Holzbalkon und Bäumen">
  <div class="host-info"><h3>Landhaus Brenner</h3><p>Lindenweg 4, 94199 Lindau<br>Wohneinheiten</p>
  <span class="host-go"><svg width="13" height="13" viewBox="0 0 13 13"><path d="M3 10 L10 3 M4.5 3 H10 V8.5" stroke="#0b72b9" stroke-width="1.6" fill="none"/></svg></span></div>
</div>
<span class="btn" style="left:543px;top:1601px;width:114px">Damit Mehr</span>

<h2 class="sec-title" style="top:1797px">Was Unsere Kunden Über <span class="accent">Uns Sagen</span></h2>

<div class="review" style="left:-205px">
  <svg class="quote" width="82" height="56" viewBox="0 0 82 56"><path d="M34 6 C16 10 6 22 6 36 C6 46 12 52 20 52 C28 52 34 46 34 39 C34 32 28 27 21 27 C19 27 17 27 16 28 C18 18 25 12 35 9 Z M78 6 C60 10 50 22 50 36 C50 46 56 52 64 52 C72 52 78 46 78 39 C78 32 72 27 65 27 C63 27 61 27 60 28 C62 18 69 12 79 9 Z" fill="none" stroke="var(--quote)" stroke-width="3"/></svg>
  <div class="avatar" role="img" aria-label="Porträtfoto des Gastes"></div>
  <div class="stars">★★★★★</div><h4>Lukas Berger</h4>
  <p>There are many variations of passages of Lorem Ipsum available, but the majority have suffered alteration in some form, by injected humour, or randomised words which don't look even slightly believable.</p>
</div>
<div class="review main" style="left:342px">
  <svg class="quote" width="82" height="56" viewBox="0 0 82 56"><path d="M34 6 C16 10 6 22 6 36 C6 46 12 52 20 52 C28 52 34 46 34 39 C34 32 28 27 21 27 C19 27 17 27 16 28 C18 18 25 12 35 9 Z M78 6 C60 10 50 22 50 36 C50 46 56 52 64 52 C72 52 78 46 78 39 C78 32 72 27 65 27 C63 27 61 27 60 28 C62 18 69 12 79 9 Z" fill="none" stroke="var(--quote)" stroke-width="3"/></svg>
  <div class="avatar" role="img" aria-label="Porträtfoto des Gastes"></div>
  <div class="stars">★★★★★</div><h4>Jonas Winter</h4>
  <p>There are many variations of passages of Lorem Ipsum available, but the majority have suffered alteration in some form, by injected humour, or randomised words which don't look even slightly believable.</p>
</div>
<div class="review" style="left:889px">
  <svg class="quote" width="82" height="56" viewBox="0 0 82 56"><path d="M34 6 C16 10 6 22 6 36 C6 46 12 52 20 52 C28 52 34 46 34 39 C34 32 28 27 21 27 C19 27 17 27 16 28 C18 18 25 12 35 9 Z M78 6 C60 10 50 22 50 36 C50 46 56 52 64 52 C72 52 78 46 78 39 C78 32 72 27 65 27 C63 27 61 27 60 28 C62 18 69 12 79 9 Z" fill="none" stroke="var(--quote)" stroke-width="3"/></svg>
  <div class="avatar" role="img" aria-label="Porträtfoto des Gastes"></div>
  <div class="stars">★★★★★</div><h4>Felix Hagen</h4>
  <p>There are many variations of passages of Lorem Ipsum available, but the majority have suffered alteration in some form, by injected humour, or randomised words which don't look even slightly believable.</p>
</div>
<svg class="abs" style="left:572px;top:2218px" width="70" height="38" viewBox="0 0 70 38">
  <path d="M12 14 L7 19 L12 24" stroke="#a9d36a" stroke-width="2" fill="none"/>
  <circle cx="47" cy="19" r="18" fill="var(--green)"/>
  <path d="M45 13 L51 19 L45 25" stroke="#fff" stroke-width="2.2" fill="none"/>
</svg>

<div class="abs map" role="img" aria-label="Kartenbereich">
  <h2 class="sec-title" style="left:0;width:918px;top:90px">So Erreichen <span class="accent">Sie Uns</span></h2>
  <a><u>Bitte akzeptieren Sie das Cookie "Externe Medien", um die Karte anzuzeigen</u></a>
</div>

<footer class="abs footer">
  <div class="f-brand"><div class="brand-dot"></div><span>Tourismusverband</span><span>Kelbach</span></div>
  <div class="f-addr">Fremdenverkehrsverein Kelbach<br>und Umgebung e. V.<br>Marktplatz 3<br>84391 Kelbach</div>
  <div class="f-col" style="left:462px"><h5>Direktlinks</h5>
    <ul><li>Kelbach</li><li>Kelbachtal-Land</li><li>Quellenland</li><li>Tourismusverband</li><li>Hügelland</li><li>Kontakt</li></ul></div>
  <div class="f-col" style="left:659px"><h5>Öffnungszeiten</h5>
    <div class="lines">Mo-Fr 9:00 – 17:00 Uhr<br>Mai-Oktober:<br>Sa 9:00-12:00 Uhr</div></div>
  <div class="f-col" style="left:875px"><h5>Kontakt</h5>
    <ul><li>Tel.: 08590 / 412 7730</li><li>Fax: 08590 / 412 7739</li><li>Info@Wanderhof-Kelbach.De</li></ul></div>
  <div class="f-rule"></div>
  <div class="f-copy">© 2025 Tourismusverband. Alle Rechte vorbehalten.</div>
  <div class="socials"><span></span><span></span><span></span><span></span></div>
</footer>

</body>
</html>
```